QRV Advisors needs a web site

We need a web site for www.qrvadvisors-example.com. QRV is a mergers and acquisition consulting company that focuses our buyer and seller services on logistics companies. We help put companies together, and help with legal and financial due diligence. We want the web site to express our service and show the logistics components. We want personalized images versus pictures of trucks and airplanes.

Our new logo uses Burgandy and grey colors. Image attached. We are not in to bold, big letters...classy, artistic, low key preferred. Confidentiality, experience, professional are what we want to express on the site.

All we expect for the first part of this project is a home page, and one subpage.  We are budgeting other funds for the technical aspects of the web site

Reason: All that I'm seeing so far is trucks, forklifts and planes. We are a legal mergers and acquisitions firm that focus on logistics. I like some of the images to say logistics, but really want it say legal, financial, and putting companies together. Will pay extra for the sub page if someone can impress us with a home page.

Reason: Swamped with another project at the moment...will work on this over the weekend and provide designer feedback and select final design by Tuesday

```html
<!DOCTYPE html>
<html lang="en">
<head>
<meta charset="utf-8">
<title>QRV Advisors</title>
<link href="https://fonts.googleapis.com/css2?family=Lato:wght@400;700&family=Open+Sans:wght@400;600;700&family=Oswald:wght@400&display=swap" rel="stylesheet">
<style>
:root{
  --brand:#c7103e;
  --brand-dark:#a50c32;
  --ink:#222;
  --body:#444;
  --topbar:#4a4646;
  --nav-active:#5a5a5a;
  --band:#ebebeb;
  --footer:#333;
  --footer-bottom:#4b4b4b;
  --white:#fff;
}
*{box-sizing:border-box;margin:0;padding:0}
html,body{width:910px;height:1200px;overflow:hidden}
body{position:relative;background:var(--white);font-family:"Open Sans",sans-serif;color:var(--body)}
.abs{position:absolute}
.topbar{left:0;top:0;width:910px;height:17px;background:var(--topbar);color:#eee;font-size:9.5px;line-height:17px}
.topbar .contact{position:absolute;right:110px;display:flex;gap:10px;align-items:center}
.topbar svg{vertical-align:-2px;margin-right:4px}
.logo{left:108px;top:36px;display:flex;align-items:center;gap:8px;font-family:"Lato",sans-serif;font-size:22px;color:#444;letter-spacing:1px}
.logo .mark{width:14px;height:14px;background:var(--brand)}
.nav{left:337px;top:48px;height:35px;display:flex}
.nav a{display:block;height:35px;line-height:35px;padding:0 11px;background:var(--brand);color:var(--white);font-size:10px;text-decoration:none;border-left:1px solid var(--brand-dark);text-transform:uppercase}
.nav a:first-child{border-left:0}
.nav a.active{background:var(--nav-active);padding:0 14px}
.rule{left:0;width:910px;height:3px;background:var(--brand)}
.hero{left:0;top:84px;width:910px;height:337px}
.hero .caption{left:333px;top:258px;font-family:"Oswald",sans-serif;color:var(--white);font-size:20px;line-height:24px;letter-spacing:-.3px}
.arrow{width:28px;height:28px;border-radius:50%;background:rgba(20,20,20,.75);display:flex;align-items:center;justify-content:center}
.welcome{left:0;top:448px;width:910px;text-align:center}
.welcome h1{font-family:"Lato",sans-serif;font-weight:400;font-size:22px;color:var(--ink)}
.welcome h1 span{color:var(--brand)}
.welcome p{width:660px;margin:6px auto 0;font-size:10.5px;line-height:16px;letter-spacing:.2px}
.band{left:0;top:570px;width:910px;height:297px;background:var(--band)}
.card{top:590px;width:225px;height:246px;background:var(--white);box-shadow:0 0 2px rgba(0,0,0,.15)}
.card h2{height:29px;line-height:29px;padding-left:13px;font-family:"Lato",sans-serif;font-weight:400;font-size:16px;color:var(--ink);border-bottom:1px solid #e2e2e2}
.card h2 span{color:var(--brand)}
.card .photo{margin:15px 0 0 12px;width:201px;height:95px;border:1px solid #ccc}
.card p{margin:10px 0 0 9px;width:212px;font-size:9.8px;line-height:15px}
.card .more{position:absolute;right:7px;bottom:5px;background:var(--brand);color:var(--white);font-size:8.5px;font-weight:700;padding:2px 5px;border:1px solid #fff;box-shadow:0 0 0 1px var(--brand)}
.news-title{left:108px;top:892px;font-family:"Lato",sans-serif;font-size:19px;color:var(--ink)}
.news-title span{color:var(--brand)}
.dots{left:760px;top:907px;display:flex;gap:4px}
.dots i{width:6px;height:6px;border-radius:50%;background:#bbb}
.dots i:first-child{background:var(--brand)}
.news-rule{left:107px;top:923px;width:694px;border-top:1px dotted #aaa}
.news-item{top:936px;width:225px;display:flex;gap:11px}
.news-item .date{width:27px;text-align:center;font-size:8px;font-weight:700;color:#666}
.news-item h3{font-size:10.5px;color:var(--brand);font-weight:600}
.news-item p{font-size:9.6px;line-height:11.5px;color:#333;margin-top:2px}
.news-sep{top:932px;width:1px;height:62px;background:#e4e4e4}
.footer{left:0;top:1020px;width:910px;height:145px;background:var(--footer);color:#eee}
.footer-bottom{left:0;top:1165px;width:910px;height:35px;background:var(--footer-bottom);color:#ccc;font-size:9.5px;line-height:35px;padding-left:111px}
.fnav{left:108px;top:1037px;display:flex;gap:19px;font-size:9.5px;color:var(--white)}
.map{left:106px;top:1070px;width:153px;height:76px;background:linear-gradient(135deg,#e6e1d6,#d9d3c3 60%,#e8b46a)}
.finfo{font-size:9.6px;line-height:18.5px;color:#ddd}
.finfo b{color:var(--white);font-weight:600}
.newsletter h2{font-family:"Lato",sans-serif;font-weight:400;font-size:22px;color:var(--white)}
.newsletter p{font-size:9.6px;line-height:13.5px;color:#ddd;margin-top:8px;width:130px}
.form{left:639px;top:1040px;width:164px;height:90px;background:#5b5b5b}
.form .field{position:absolute;left:7px;width:150px;height:19px;background:var(--white);font-size:9px;line-height:19px;padding-left:5px;color:#555}
.form .btn{position:absolute;left:7px;top:58px;background:var(--brand);color:var(--white);font-weight:700;font-size:12px;padding:2px 6px;border-radius:2px}
.social{right:110px;top:1176px;display:flex;gap:12px}
.social i{width:13px;height:13px;border-radius:50%;background:#ddd}
</style>
</head>
<body>

<div class="abs topbar">
  <div class="contact">
    <span><svg width="9" height="10" viewBox="0 0 9 10"><path d="M2 0l2 2.5-1 1.3c.6 1.3 1.4 2.1 2.5 2.7L7 5.5 9 7.6 7.6 9.6C3.6 9 .4 5.6 0 1.6z" fill="#ccc"/></svg>Call: 555-010-2040</span>
    <span><svg width="12" height="9" viewBox="0 0 12 9"><rect width="12" height="9" fill="#bbb"/><path d="M0 0l6 5 6-5" stroke="#555" fill="none"/></svg>info@qrvadvisors-example.com</span>
  </div>
</div>

<div class="abs logo"><span class="mark"></span>QRV Advisors</div>

<nav class="abs nav">
  <a class="active">Home</a><a>About</a><a>Consulting Services</a><a>News &amp; Events</a><a>FAQ's</a><a>Contact</a>
</nav>
<div class="abs rule" style="top:81px"></div>

<section class="abs hero">
  <svg width="910" height="337" role="img" aria-label="Hero banner: red truck on a highway, two businessmen shaking hands before a glass tower, city highway at night with light trails">
    <defs>
      <linearGradient id="road" x1="0" y1="0" x2="0" y2="1"><stop offset="0" stop-color="#a9c2d6"/><stop offset=".45" stop-color="#8a9a55"/><stop offset="1" stop-color="#6a6a62"/></linearGradient>
      <linearGradient id="tower" x1="0" y1="0" x2="1" y2="1"><stop offset="0" stop-color="#b9c8ea"/><stop offset=".5" stop-color="#3f5e9a"/><stop offset="1" stop-color="#1c2a4a"/></linearGradient>
      <linearGradient id="night" x1="0" y1="0" x2="0" y2="1"><stop offset="0" stop-color="#0c1a4a"/><stop offset=".6" stop-color="#1d3d8a"/><stop offset="1" stop-color="#6f7d99"/></linearGradient>
    </defs>
    <polygon points="0,0 282,0 318,337 0,337" fill="url(#road)"/>
    <polygon points="284,0 603,0 652,337 320,337" fill="url(#tower)"/>
    <polygon points="605,0 910,0 910,337 654,337" fill="url(#night)"/>
    <line x1="283" y1="0" x2="319" y2="337" stroke="#fff" stroke-width="3"/>
    <line x1="604" y1="0" x2="653" y2="337" stroke="#fff" stroke-width="3"/>
    <rect x="320" y="252" width="312" height="85" fill="rgba(20,20,30,.45)"/>
  </svg>
  <div class="abs caption">We offer business planning and merger<br>and acquisition(M&amp;A) advisory services.</div>
  <div class="abs arrow" style="left:110px;top:144px"><svg width="8" height="12"><path d="M7 1L2 6l5 5" stroke="#fff" fill="none" stroke-width="1.5"/></svg></div>
  <div class="abs arrow" style="left:785px;top:144px"><svg width="8" height="12"><path d="M1 1l5 5-5 5" stroke="#fff" fill="none" stroke-width="1.5"/></svg></div>
</section>
<div class="abs rule" style="top:421px"></div>

<section class="abs welcome">
  <h1>Welcome To <span>QRV Advisors</span></h1>
  <p>QRV assists business owners within the logistics industry to implement growth and exit strategies.QRV services are offered by industry executives with extensive M&amp;A experience. Your company will benefit from a unique and outside perspective from consultants that understand your business.QRV can help you formulate and execute your growth strategy. We take a strategic and consultative approach with our advisory services that will help you grow your business effectively.</p>
</section>

<div class="abs band"></div>

<article class="abs card" style="left:106px">
  <h2>Business <span>Planning</span></h2>
  <div class="photo" role="img" aria-label="Team of colleagues meeting around a laptop" style="background:linear-gradient(135deg,#eee,#9a9a9a 60%,#d8d8d8)"></div>
  <p>Lorem ipsum dolor sit amet, consectetuer in adipiscing elit,Sed diam nonummy nibhaops euismod tincidunt ut laoreet dolore magnad aliquam erat volutpat. Ut wisi enim adminio veniam, quis nostrud exerci tationdada .</p>
  <span class="more">Learn more »</span>
</article>
<article class="abs card" style="left:341px">
  <h2>Business <span>Merger</span></h2>
  <div class="photo" role="img" aria-label="Handshake against a blue sky and office towers" style="background:linear-gradient(180deg,#0c2a6a,#3f6cb5 55%,#b9c6db)"></div>
  <p>Lorem ipsum dolor sit amet, consectetuer in adipiscing elit,Sed diam nonummy nibhaops euismod tincidunt ut laoreet dolore magnad aliquam erat volutpat. Ut wisi enim adminio veniam, quis nostrud exerci tationdada .</p>
  <span class="more">Learn more »</span>
</article>
<article class="abs card" style="left:578px">
  <h2>Acquisition <span>(M&amp;A) Advisory</span></h2>
  <div class="photo" role="img" aria-label="Advisor reviewing documents with a couple" style="background:linear-gradient(90deg,#2c3444,#c9a58e 55%,#8c94a6)"></div>
  <p>Lorem ipsum dolor sit amet, consectetuer in adipiscing elit,Sed diam nonummy nibhaops euismod tincidunt ut laoreet dolore magnad aliquam erat volutpat. Ut wisi enim adminio veniam, quis nostrud exerci tationdada .</p>
  <span class="more">Learn more »</span>
</article>

<h2 class="abs news-title">Latest <span>News</span></h2>
<div class="abs dots"><i></i><i></i><i></i><i></i></div>
<div class="abs news-rule"></div>

<div class="abs news-item" style="left:107px">
  <div class="date"><svg width="25" height="24" viewBox="0 0 25 24"><rect x="1" y="3" width="23" height="20" fill="#fff" stroke="#999"/><rect x="1" y="3" width="23" height="4" fill="#999"/><text x="12.5" y="19" font-size="10" text-anchor="middle" fill="#c7103e" font-family="Open Sans,sans-serif">10</text></svg>FEB</div>
  <div><h3>Lorem ipsum dolor sit amet</h3><p>Lorem ipsum dolor sit amet, in to adips consectetit uer adipiscing elit, sed diam nonummy oll euismod tincidunt aliquam.</p></div>
</div>
<div class="abs news-sep" style="left:333px"></div>
<div class="abs news-item" style="left:350px">
  <div class="date"><svg width="25" height="24" viewBox="0 0 25 24"><rect x="1" y="3" width="23" height="20" fill="#fff" stroke="#999"/><rect x="1" y="3" width="23" height="4" fill="#999"/><text x="12.5" y="19" font-size="10" text-anchor="middle" fill="#c7103e" font-family="Open Sans,sans-serif">10</text></svg>FEB</div>
  <div><h3>Lorem ipsum dolor sit amet</h3><p>Lorem ipsum dolor sit amet, in to adips consectetit uer adipiscing elit, sed diam nonummy oll euismod tincidunt aliquam.</p></div>
</div>
<div class="abs news-sep" style="left:577px"></div>
<div class="abs news-item" style="left:594px">
  <div class="date"><svg width="25" height="24" viewBox="0 0 25 24"><rect x="1" y="3" width="23" height="20" fill="#fff" stroke="#999"/><rect x="1" y="3" width="23" height="4" fill="#999"/><text x="12.5" y="19" font-size="10" text-anchor="middle" fill="#c7103e" font-family="Open Sans,sans-serif">10</text></svg>FEB</div>
  <div><h3>Lorem ipsum dolor sit amet</h3><p>Lorem ipsum dolor sit amet, in to adips consectetit uer adipiscing elit, sed diam nonummy oll euismod tincidunt aliquam.</p></div>
</div>

<footer class="abs footer"></footer>
<div class="abs fnav"><span>Home</span><span>About</span><span>Consulting Services</span><span>News &amp; Events</span><span>Faq's</span><span>Contact</span></div>
<div class="abs map" role="img" aria-label="Street map showing the office location"></div>

<div class="abs finfo" style="left:269px;top:1066px">
  <svg class="abs" style="left:0;top:5px" width="8" height="11" viewBox="0 0 8 11"><path d="M4 0a4 4 0 0 1 4 4c0 3-4 7-4 7S0 7 0 4a4 4 0 0 1 4-4z" fill="#bbb"/><circle cx="4" cy="4" r="1.5" fill="#333"/></svg>
  <div style="margin-left:15px"><b>Location</b><br>Main office Location,<br>Lane no. Po box 123<br>City, Zip 0000123</div>
</div>
<div class="abs finfo" style="left:390px;top:1069px">
  <svg class="abs" style="left:0;top:5px" width="9" height="10" viewBox="0 0 9 10"><path d="M2 0l2 2.5-1 1.3c.6 1.3 1.4 2.1 2.5 2.7L7 5.5 9 7.6 7.6 9.6C3.6 9 .4 5.6 0 1.6z" fill="#bbb"/></svg>
  <div style="margin-left:17px"><b>Phone:</b><br>555-010-2040<br><b>FAX:</b><br>555-010-2041</div>
</div>

<div class="abs newsletter" style="left:510px;top:1036px">
  <h2>Newsletter</h2>
  <p>Get Valuable Tips and News from QRV, Signup to our Monthly Newsletter today!</p>
</div>
<div class="abs form">
  <div class="field" style="top:7px">Name</div>
  <div class="field" style="top:33px">Email</div>
  <span class="btn">Subscribe</span>
</div>

<div class="abs footer-bottom">© Copyright 2013 QRV Advisors.</div>
<div class="abs social"><i></i><i></i><i></i></div>

</body>
</html>
```